Investment Advisor E-Newsletter Banner Design

I need a banner designed for an email newsletter that will be sent monthly to clients and prospects. We want to see designs that are elegant and use our logo well. The banner should be 922x150px and should go well with the www.tlvbanda.com website. Should include Logo and email and phone number.

Target Market(s)

High net worth investors

Number of Pages Required

1 page

Requirements
Must have
• logo, place for email (info@tlvbanda.com) and phone number (415-297-6180), colors and design that work well with www.tlvbanda.com website

```html
<!DOCTYPE html>
<html lang="en">
<head>
<meta charset="utf-8">
<title>Talvera Banda Capital Advisors – Newsletter Banner</title>
<link href="https://fonts.googleapis.com/css2?family=Cormorant+Garamond:ital,wght@0,600;1,500&display=swap" rel="stylesheet">
<style>
  :root {
    --brand-blue: #2c2f8e;
    --ink-dark: #1b1b1d;
    --panel-white: #ffffff;
    --shelf-deep: #161210;
    --shelf-warm: #5a4632;
    --shelf-mid: #2e2520;
    --book-amber: #8a6a48;
    --skin-glow: #b98a74;
    --suit-blue: #2d4a6a;
    --text-light: #ffffff;
  }
  html, body {
    margin: 0;
    padding: 0;
    width: 1200px;
    height: 195px;
    overflow: hidden;
    background: var(--panel-white);
  }
  .banner {
    position: relative;
    width: 1200px;
    height: 195px;
    overflow: hidden;
    font-family: "Cormorant Garamond", Georgia, serif;
  }
  .banner__photo {
    position: absolute;
    inset: 0;
    background:
      radial-gradient(ellipse 120px 95px at 945px 75px, rgba(205,150,125,0.75), transparent 75%),
      radial-gradient(ellipse 150px 70px at 1010px 195px, rgba(45,74,106,0.95), transparent 80%),
      radial-gradient(ellipse 60px 50px at 500px 105px, rgba(175,125,100,0.55), transparent 75%),
      radial-gradient(ellipse 55px 45px at 790px 120px, rgba(170,120,95,0.5), transparent 75%),
      radial-gradient(ellipse 80px 40px at 560px 190px, rgba(40,70,80,0.7), transparent 80%),
      radial-gradient(ellipse 70px 40px at 830px 190px, rgba(120,40,40,0.6), transparent 80%),
      radial-gradient(ellipse 70px 35px at 660px 20px, rgba(138,106,72,0.7), transparent 75%),
      radial-gradient(ellipse 60px 35px at 645px 85px, rgba(138,106,72,0.6), transparent 75%),
      radial-gradient(ellipse 70px 30px at 850px 85px, rgba(138,106,72,0.6), transparent 75%),
      radial-gradient(ellipse 40px 60px at 1130px 60px, rgba(138,106,72,0.45), transparent 75%),
      radial-gradient(ellipse 60px 40px at 595px 160px, rgba(138,106,72,0.5), transparent 75%),
      linear-gradient(90deg, var(--shelf-mid) 0%, #3b2f26 40%, var(--shelf-mid) 60%, #241d19 80%, var(--shelf-deep) 100%);
  }
  .banner__panel {
    position: absolute;
    top: 0;
    left: 0;
    width: 500px;
    height: 195px;
  }
  .brand {
    position: absolute;
    top: 24px;
    left: 26px;
    display: flex;
    align-items: center;
    gap: 22px;
  }
  .brand__mark {
    width: 76px;
    height: 76px;
    border-radius: 50%;
    background: var(--brand-blue);
    flex: none;
  }
  .brand__name {
    margin: 0;
    color: var(--brand-blue);
    font-weight: 600;
    line-height: 1.05;
  }
  .brand__name-main {
    display: block;
    font-size: 44px;
  }
  .brand__name-sub {
    display: block;
    font-size: 25px;
    margin-top: 6px;
  }
  .contact {
    position: absolute;
    bottom: 0;
    height: 39px;
    display: flex;
    align-items: center;
    gap: 14px;
    color: var(--text-light);
    font-style: italic;
    font-weight: 500;
    font-size: 20px;
  }
  .contact--email {
    left: 0;
    width: 248px;
    padding-left: 12px;
    box-sizing: border-box;
    background: var(--brand-blue);
    border-radius: 0 20px 0 0;
    z-index: 2;
  }
  .contact--phone {
    left: 242px;
    width: 220px;
    padding-left: 22px;
    box-sizing: border-box;
    background: var(--ink-dark);
    border-radius: 20px 20px 0 0;
    z-index: 1;
  }
  .contact__icon {
    width: 28px;
    height: 28px;
    border-radius: 50%;
    background: var(--text-light);
    display: flex;
    align-items: center;
    justify-content: center;
    flex: none;
  }
</style>
</head>
<body>
  <div class="banner">
    <div class="banner__photo" role="img" aria-label="Photo of smiling advisors meeting in a warm wood library with bookshelves"></div>

    <svg class="banner__panel" viewBox="0 0 500 195" aria-hidden="true">
      <polygon points="0,0 484,0 434,195 0,195" fill="var(--panel-white)"/>
      <polygon points="484,0 496,0 446,195 434,195" fill="var(--ink-dark)"/>
    </svg>

    <div class="brand">
      <div class="brand__mark"></div>
      <p class="brand__name">
        <span class="brand__name-main">Talvera Banda</span>
        <span class="brand__name-sub">Capital Advisors</span>
      </p>
    </div>

    <div class="contact contact--email">
      <span class="contact__icon">
        <svg width="16" height="12" viewBox="0 0 16 12" aria-hidden="true">
          <rect x="0" y="0" width="16" height="12" rx="1.5" fill="var(--brand-blue)"/>
          <polyline points="1,1.5 8,7 15,1.5" fill="none" stroke="#fff" stroke-width="1.4"/>
        </svg>
      </span>
      <span class="contact__text">info@tlvbanda.com</span>
    </div>

    <div class="contact contact--phone">
      <span class="contact__icon">
        <svg width="16" height="16" viewBox="0 0 24 24" aria-hidden="true">
          <path fill="var(--ink-dark)" d="M6.6 10.8a15.1 15.1 0 0 0 6.6 6.6l2.2-2.2a1 1 0 0 1 1-.25 11.4 11.4 0 0 0 3.6.57 1 1 0 0 1 1 1V20a1 1 0 0 1-1 1A17 17 0 0 1 3 4a1 1 0 0 1 1-1h3.5a1 1 0 0 1 1 1c0 1.250.2 2.45.57 3.57a1 1 0 0 1-.25 1z"/>
        </svg>
      </span>
      <span class="contact__text">415-297-6180</span>
    </div>
  </div>
</body>
</html>
```